Harbor Loom Floors Letterhead

Letterhead used for business reasons. It must be editable and easy to use.

Address is 2715 W. Pelican Lane Marlow Bay GA 34187 - 555.382.6519

```html
<!DOCTYPE html>
<html lang="en">
<head>
<meta charset="utf-8">
<title>Harbor Loom Floors Letterhead</title>
<link href="https://fonts.googleapis.com/css2?family=Montserrat:wght@400;500&family=Lato:wght@400;700&family=Dancing+Script:wght@600&display=swap" rel="stylesheet">
<style>
  :root {
    --backdrop: #e9e7e4;
    --paper: #ffffff;
    --ink: #1a1a1a;
    --header-black: #1b1b1b;
    --accent-orange: #e08a24;
    --accent-grey: #9b9593;
    --muted: #333333;
  }
  * { box-sizing: border-box; margin: 0; padding: 0; }
  html, body {
    width: 1200px; height: 1200px; overflow: hidden;
    background: var(--backdrop);
  }
  .letterhead {
    position: absolute; left: 204px; top: 40px;
    width: 792px; height: 1120px;
    background: var(--paper);
    box-shadow: 0 6px 24px rgba(0,0,0,0.12);
    overflow: hidden;
    font-family: "Lato", sans-serif;
    color: var(--ink);
  }
  .header-band { position: absolute; left: 0; top: 0; width: 792px; height: 240px; }
  .brand {
    position: absolute; right: 58px; top: 50px;
    font-family: "Montserrat", sans-serif; font-weight: 500;
    font-size: 26px; color: var(--accent-orange);
    letter-spacing: 0.5px;
  }
  .sender {
    position: absolute; left: 62px; top: 234px;
    font-family: "Montserrat", sans-serif; font-style: normal; font-size: 12px;
    line-height: 1.45; color: var(--muted);
  }
  .sender .phone { display: flex; align-items: center; gap: 6px; margin-top: 4px; }
  .sender svg { width: 11px; height: 11px; }
  .letter-body { position: absolute; left: 110px; top: 330px; width: 600px; font-size: 13px; line-height: 1.35; }
  .date { font-family: "Montserrat", sans-serif; font-size: 14px; margin-bottom: 22px; }
  .recipient { font-family: "Montserrat", sans-serif; font-size: 13px; margin-bottom: 22px; }
  .recipient p { line-height: 1.3; }
  .recipient .block { margin-bottom: 20px; }
  .salutation { font-weight: 700; font-size: 16px; margin: 6px 0 26px; }
  .paragraph { margin-bottom: 22px; }
  .closing { margin-top: 30px; font-size: 13px; }
  .signature {
    margin-top: 34px;
    font-family: "Dancing Script", cursive; font-size: 40px; font-weight: 600;
  }
</style>
</head>
<body>
<main class="letterhead">
  <svg class="header-band" viewBox="0 0 792 240" aria-hidden="true">
    <path d="M0 0 H792 V150 C640 152 470 128 300 150 C170 168 70 190 0 200 Z" fill="var(--header-black)"/>
    <path d="M0 200 C70 190 170 168 300 150 C470 128 600 140 680 150 C590 142 460 140 300 160 C180 176 80 205 0 225 Z" fill="var(--accent-orange)"/>
    <path d="M330 162 C480 140 640 148 792 150 V170 C650 160 500 152 330 162 Z" fill="var(--accent-grey)"/>
  </svg>

  <div class="brand">Harbor Loom Floors</div>

  <address class="sender">
    <p>2715 W. Pelican Lane</p>
    <p>Marlow Bay GA 34187</p>
    <p class="phone">
      <svg viewBox="0 0 12 12"><path d="M3 1 L5 3.4 L4 4.6 C4.6 6 6 7.4 7.4 8 L8.6 7 L11 9 L9.8 10.8 C5.6 10.4 1.6 6.4 1.2 2.2 Z" fill="var(--accent-orange)"/></svg>
      555.382.6519
    </p>
  </address>

  <section class="letter-body">
    <p class="date">January-03-2020</p>
    <div class="recipient">
      <div class="block">
        <p>Mr. Owen Castell</p>
        <p>President</p>
      </div>
      <p>Brightway Holdings</p>
      <p>123 Street Name, Suite# 10</p>
      <p>City, State, 120023</p>
    </div>
    <p class="salutation">Dear Mr. Owen</p>
    <p class="paragraph">Lorem ipsum dolor sit amet, consectetur adipiscing elit, sed do eiusmod tempor incididunt ut labore et dolore magna aliqua. Ut enim ad minim veniam, quis nostrud exercitation ullamco laboris nisi ut aliquip ex ea commodo consequat. Duis aute irure dolor in reprehenderit in voluptate velit esse cillum dolore eu fugiat nulla pariatur.</p>
    <p class="paragraph">Lorem ipsum dolor sit amet, consectetur adipiscing elit, sed do eiusmod tempor incididunt ut labore et dolore magna aliqua. Ut enim ad minim veniam, quis nostrud exercitation ullamco laboris nisi ut aliquip ex ea commodo consequat. Duis aute irure dolor in reprehenderit in voluptate velit esse cillum dolore eu fugiat nulla pariatur.</p>
    <p class="paragraph">Lorem ipsum dolor sit amet, consectetur adipiscing elit, sed do eiusmod tempor incididunt ut labore et dolore magna aliqua. Ut enim ad minim veniam, quis nostrud exercitation ullamco laboris nisi ut aliquip ex ea commodo consequat.</p>
    <p class="paragraph">Excepteur sint occaecat cupidatat non proident, sunt in culpa qui officia deserunt mollit anim id est laborum. re et dolore magnam aliquam quaerat voluptatem.</p>
    <p class="closing">Regards</p>
    <p class="signature">Dana Whitfield</p>
  </section>
</main>
</body>
</html>
```